Venture Capital firm needs modern business cards

We are a Venture Capital firm within financial services/Asset management. The industry generally has basic business cards with black, blue and maybe green/yellow design elements.
Our firm has a four-colour swoosh logo. We are based in London and want to stand out, just a little bit!, from the crowd. Our company is called LORV Investments and the 'C' stands for collaboration thus using makerswarm is a natural portal for our business card design competition. Our logo came via makerswarm too!
We use 'Venture Partner in Asset Management' as our tagline and this is Trademark registered. We operate in a conservative industry and we should not overstep our mark. The logo is colorful as it is and therefore the rest of the design should not be too fanciful.
The objective is twofold: make our logo element stick and memorable with our audience, whilst representing a conservative yet young image.
Updates
The Business Card obviously needs a field for Name, Surname, Job Title, Adress fields: Street, City, Postcode, Country, telefone and cell number, website address, etc.
We have uploaded the ai file. We trust that these are OK. If not, please advise.
Reason: We have have been busy with a client engagement. We will set the project as Guaranteed in return for the troubles we cause. Apologies for the confusion.
Thank you all for these great and creative design suggestions. The team is very happy with a number of your ideas! We will be in touch tomorrow to give individual feedback before the project closes on Friday. We look forward to working with some of you to narrow down your creations. Thank you, LORV Investments team.
All,
Target Market(s)
Financial Services Professionals, Investors, Media, 35-70 years, mainly male, well educated
Industry/Entity Type
Conservative
Requirements
Must have
- We must make use of our logo and potential tagline 'Venture Partner in Asset Management' as we are establishing a new Brand and new company in the market.
We can use 'LORV', 'LORV Investments', and 'LORV Investments'+tagline 'Venture Partner in Asset Management' or simply the four-colour swoosh plus the name of the company as part of the text. (see files)
All design elements are available in black or grey-scale if required. (grey scale swoosh attached).
Due to regulation we must have the following wording on the card in small print 'LORV Investments is an Appointed Representative of Bramwell Holdings Partnership Limited, which is authorised by the Monetary Oversight Board'.
Nice to have
- We would consider designs that make use of different printing techniques such embossing/debossing, UV spot etc.
We attach our colour palette in the files section for your reference.
Should not have
- The font we use for our company name is 'EXO' so do not use a font style that clashes with the corporate fonts, please.
Do not use other design elements than the ones we provide in the file library as part of this project.

```html
<!DOCTYPE html>
<html lang="en">
<head>
<meta charset="utf-8">
<title>LORV Investments – Business Card</title>
<link rel="stylesheet" href="https://fonts.googleapis.com/css2?family=Fira+Sans:wght@400;500&display=swap">
<style>
  :root {
    --stage: #e6e3df;
    --card-back: #2a2a2c;
    --card-front: #ffffff;
    --ink: #3d3d40;
    --ink-soft: #55575b;
    --mark-light: #8a8b8f;
    --accent-blue: #7cc3dc;
    --accent-red: #c41e4a;
  }
  * { margin: 0; padding: 0; box-sizing: border-box; }
  html, body {
    width: 1200px; height: 716px; overflow: hidden;
    background: var(--stage);
  }
  body {
    font-family: "Fira Sans", Arial, sans-serif;
    color: var(--ink);
    position: relative;
  }
  .card {
    position: absolute;
    top: 208px;
    width: 520px; height: 300px;
    border-radius: 6px;
    box-shadow: 0 6px 18px rgba(0,0,0,0.18);
  }
  /* Back side */
  .card-back {
    left: 60px;
    background: var(--card-back);
    display: flex; align-items: center; justify-content: center; gap: 14px;
  }
  .card-back .brand-dot {
    width: 22px; height: 22px; border-radius: 50%;
    background: var(--accent-red);
  }
  .card-back .brand-name {
    font-weight: 500; font-size: 46px; letter-spacing: 2px;
    color: var(--mark-light);
  }
  /* Front side */
  .card-front {
    left: 620px;
    background: var(--card-front);
  }
  .brand {
    position: absolute; left: 34px; top: 30px;
    display: flex; align-items: center; gap: 12px;
  }
  .brand-dot {
    width: 20px; height: 20px; border-radius: 50%;
    background: var(--accent-red);
  }
  .brand-name {
    font-weight: 500; font-size: 44px; line-height: 1; letter-spacing: 1px;
    color: var(--ink);
  }
  .brand-sub {
    position: absolute; left: 118px; top: 76px;
    font-size: 11px; letter-spacing: 4px; color: var(--ink-soft);
  }
  .person { position: absolute; left: 34px; top: 110px; }
  .person-name { font-weight: 500; font-size: 18px; color: var(--ink); }
  .person-title { font-size: 12px; margin-top: 3px; color: var(--ink-soft); }
  .website {
    position: absolute; left: 34px; top: 172px;
    font-size: 13px; color: var(--ink);
    padding-bottom: 3px; border-bottom: 1px solid var(--accent-blue);
  }
  .legal {
    position: absolute; left: 34px; top: 214px; width: 300px;
    font-size: 8px; line-height: 1.35; font-style: normal; color: var(--ink-soft);
  }
  .contact {
    position: absolute; right: 32px; bottom: 30px;
    font-size: 13px; line-height: 1.4; color: var(--ink);
  }
  .contact-row { display: flex; gap: 10px; }
  .contact-row .label { width: 12px; color: var(--ink-soft); }
  .address { margin-top: 6px; }
</style>
</head>
<body>
  <section class="card card-back" aria-label="Business card back">
    <span class="brand-dot"></span>
    <span class="brand-name">LORV</span>
  </section>

  <section class="card card-front" aria-label="Business card front">
    <div class="brand">
      <span class="brand-dot"></span>
      <span class="brand-name">LORV</span>
    </div>
    <div class="brand-sub">Investments</div>

    <div class="person">
      <div class="person-name">Julian Marcus Hale</div>
      <div class="person-title">Founder &amp; CEO</div>
    </div>

    <div class="website">www.lorv.com</div>

    <p class="legal">LORV Investments is an Appointed Representative of Bramwell Holdings Partnership Limited, which is authorised by the Monetary Oversight Board</p>

    <div class="contact">
      <div class="contact-row"><span class="label">T</span><span>917 555 0188</span></div>
      <div class="contact-row"><span class="label">M</span><span>917 555 0188</span></div>
      <div class="contact-row"><span class="label">E</span><span>julian@lorv.com</span></div>
      <div class="address">Alvarado 14. Col. Roma<br>Country DF 06700. MX.</div>
    </div>
  </section>
</body>
</html>
```